Fabric Store Business card

Need a business card portraying store logo and up and coming business of quilt fabrics, apparel fabrics, notions and buttons. Our business name is Gilded Thimble and Beyond. Am attaching logo. The design should communicate a growing business and warm atmosphere. Would like address and store hours and contact info displayed on card. Mon - Fri 9:30 to 5:00, Saturday 9:30 to 1:00. Address 784 W Orchard Ave, Newton, KS 67230 email: gildedthimblebeyond@mailvexa.com. Phone and fax 316-527-3486. After hours contact # 620-431-9052 Also like vintage sewing machines and dress forms if it works to incorporate fine, if not thats ok too.
Store

```html
<!DOCTYPE html>
<html lang="en">
<head>
<meta charset="utf-8">
<title>Gilded Thimble and Beyond – Business Card</title>
<link rel="stylesheet" href="https://fonts.googleapis.com/css2?family=Oswald:wght@400;500&family=Roboto+Condensed:wght@400&display=swap">
<style>
  :root {
    --backdrop: #6f6f6f;
    --card: #f7f7f7;
    --card-shade: #e9e9e9;
    --red: #cc2b3b;
    --maroon: #9b1f2d;
    --ink: #b42434;
    --text: #3a3a3a;
    --muted: #555555;
  }
  * { box-sizing: border-box; margin: 0; padding: 0; }
  html, body { width: 1200px; height: 908px; overflow: hidden; }
  body {
    background: var(--backdrop);
    position: relative;
    font-family: "Roboto Condensed", "Arial Narrow", sans-serif;
  }
  .card {
    position: absolute;
    width: 540px;
    height: 310px;
    background: linear-gradient(160deg, #ffffff 0%, var(--card) 55%, var(--card-shade) 100%);
    box-shadow: 0 10px 24px rgba(0,0,0,0.35);
    overflow: hidden;
  }
  .card--front { left: 50px; top: 110px; }
  .card--back { left: 610px; top: 480px; }

  .brand {
    position: absolute;
    display: flex;
    align-items: center;
    gap: 12px;
  }
  .brand__dot {
    width: 38px; height: 38px;
    border-radius: 50%;
    background: var(--red);
    flex: none;
  }
  .brand__name {
    font-family: "Oswald", "Arial Narrow", sans-serif;
    font-weight: 400;
    color: var(--ink);
    font-size: 26px;
    letter-spacing: 0.5px;
    white-space: nowrap;
  }
  .card--front .brand { left: 50%; top: 118px; transform: translateX(-50%); }
  .card--back .brand { left: 175px; top: 54px; }
  .card--back .brand__dot { width: 30px; height: 30px; }
  .card--back .brand__name { font-size: 21px; }

  .band { position: absolute; bottom: 0; height: 34px; }
  .card--front .band--left { left: 0; width: 296px; background: var(--red); }
  .card--front .band--right { left: 300px; right: 0; background: var(--maroon); }
  .card--back .band { height: 24px; }
  .card--back .band--left { left: 0; width: 356px; background: var(--maroon); }
  .card--back .band--right { left: 362px; right: 0; background: var(--red); }

  .rule {
    position: absolute;
    left: 0; right: 0; top: 122px;
    height: 2px;
    background: var(--red);
  }
  .address {
    position: absolute;
    right: 22px; top: 132px;
    text-align: right;
    font-size: 12px;
    line-height: 15px;
    color: var(--text);
  }
  .hours {
    position: absolute;
    right: 22px; top: 168px;
    text-align: right;
    font-size: 10px;
    line-height: 14px;
    color: var(--muted);
  }
  .identity {
    position: absolute;
    left: 26px; top: 180px;
    display: flex;
    align-items: center;
    font-family: "Oswald", "Arial Narrow", sans-serif;
    text-transform: uppercase;
    color: var(--ink);
  }
  .identity__name { font-size: 17px; font-weight: 500; letter-spacing: 0.5px; }
  .identity__role {
    font-size: 11px;
    letter-spacing: 1px;
    margin-left: 7px;
    padding-left: 7px;
    border-left: 1.5px solid var(--ink);
  }
  .contacts {
    position: absolute;
    left: 26px; top: 210px;
    list-style: none;
  }
  .contacts li {
    display: flex;
    align-items: center;
    gap: 7px;
    font-size: 9.5px;
    color: var(--muted);
    height: 16px;
    white-space: nowrap;
  }
  .contacts svg { width: 12px; height: 12px; flex: none; }
</style>
</head>
<body>
  <section class="card card--front" aria-label="Card front">
    <div class="brand">
      <span class="brand__dot"></span>
      <span class="brand__name">Gilded Thimble and Beyond</span>
    </div>
    <div class="band band--left"></div>
    <div class="band band--right"></div>
  </section>

  <section class="card card--back" aria-label="Card back">
    <div class="brand">
      <span class="brand__dot"></span>
      <span class="brand__name">Gilded Thimble and Beyond</span>
    </div>
    <div class="rule"></div>
    <p class="address">784 W Orchard Ave,<br>Newton, KS 67230</p>
    <p class="hours">Mon – Fri 9:30 to 5:00<br>Saturday 9:30 to 1:00</p>
    <div class="identity">
      <span class="identity__name">Mara Ellison</span>
      <span class="identity__role">General Manager</span>
    </div>
    <ul class="contacts">
      <li>
        <svg viewBox="0 0 12 12"><rect width="12" height="12" rx="2" fill="#cc2b3b"/><path d="M3.6 2.8l1.2 1.4-.7.8c.4 1 1.1 1.8 2.1 2.3l.8-.7 1.4 1.2-.7 1.3C5.4 8.8 3.2 6.6 3 3.5z" fill="#fff"/></svg>
        316-527-3486 (phone &amp; fax)
      </li>
      <li>
        <svg viewBox="0 0 12 12"><rect width="12" height="12" rx="2" fill="#cc2b3b"/><rect x="4" y="2.5" width="4" height="7" rx="0.8" fill="#fff"/></svg>
        620-431-9052 (after hours)
      </li>
      <li>
        <svg viewBox="0 0 12 12"><rect width="12" height="12" rx="2" fill="#cc2b3b"/><rect x="2.5" y="3.5" width="7" height="5" fill="#fff"/><path d="M2.5 3.5L6 6.4 9.5 3.5" fill="none" stroke="#cc2b3b" stroke-width="0.8"/></svg>
        gildedthimblebeyond@mailvexa.com
      </li>
      <li>
        <svg viewBox="0 0 12 12"><rect width="12" height="12" rx="2" fill="#cc2b3b"/><circle cx="6" cy="6" r="3.3" fill="none" stroke="#fff" stroke-width="0.9"/><path d="M2.7 6h6.6M6 2.7c-1.6 2-1.6 4.6 0 6.6M6 2.7c1.6 2 1.6 4.6 0 6.6" fill="none" stroke="#fff" stroke-width="0.7"/></svg>
        www.gildedthimblebeyond.shop
      </li>
    </ul>
    <div class="band band--left"></div>
    <div class="band band--right"></div>
  </section>
</body>
</html>
```